Business Card Design for Technology Company

New business card design needed for technology company director.
Ideally, the design will fit the style and nature of the industry. We are a supplier of quality products and services, and we hope the design will give customers and suppliers this impression.

Target Market(s)

3D Printing Industry

Industry/Entity Type

Technology Equipment

Contact Information for Business Card

Name: Marcus Lin
Title: Director
Company address: Factory K4, 7B Harlowe Road, Springvale Victoria Australia 3150
Telephone: +61-3-8555 6413
Email: marcus.lin@vortalmake.com.au
Website: www.vortalmake.com.au

Requirements
Must have
• All information in business card details
• Company logo
• '3D Printers and 3D Print Filaments' at proper place
Nice to have
• Style to fit the industry
• Colour to fit logo

```html
<!DOCTYPE html>
<html lang="en">
<head>
<meta charset="utf-8">
<title>Vortal Make – Business Card</title>
<link rel="stylesheet" href="https://fonts.googleapis.com/css2?family=Exo+2:wght@700;800&family=Lato:ital,wght@0,400;0,700;1,400&display=swap">
<style>
  :root {
    --backdrop: #e4e4e4;
    --blue-deep: #0a5fa3;
    --blue-mid: #0b7fc4;
    --blue-light: #0fa3dd;
    --blue-edge: #053d73;
    --orange: #f7941d;
    --orange-light: #ffb545;
    --paper-white: #f7f7f7;
    --paper-grey: #dcdcdc;
    --ink-dark: #1c1c1c;
    --ink-white: #ffffff;
    --ink-grey: #8a8a8a;
    --card-black: #000000;
    --partner-green: #1f7a52;
    --partner-blue: #2a74b8;
    --flag-navy: #1f3b7a;
  }
  html, body {
    margin: 0;
    padding: 0;
    width: 1125px;
    height: 1200px;
    overflow: hidden;
    background: var(--backdrop);
  }
  .canvas {
    position: relative;
    width: 1125px;
    height: 1200px;
  }
  .card {
    position: absolute;
    left: 150px;
    width: 825px;
    height: 473px;
    display: block;
    box-shadow: 0 2px 4px rgba(0,0,0,0.25);
  }
  .card--front { top: 108px; }
  .card--back { top: 619px; }
  .name { font-family: "Exo 2", sans-serif; font-weight: 800; font-size: 31px; fill: var(--ink-white); letter-spacing: 0.5px; }
  .role { font-family: "Lato", sans-serif; font-weight: 700; font-size: 20px; fill: var(--ink-white); letter-spacing: 0.5px; }
  .detail { font-family: "Lato", sans-serif; font-weight: 400; font-size: 19px; fill: var(--ink-white); }
  .brand-name { font-family: "Lato", sans-serif; font-weight: 700; fill: var(--ink-dark); letter-spacing: 3px; }
  .brand-name--back { fill: var(--ink-white); }
  .tagline { font-family: "Lato", sans-serif; font-weight: 400; font-size: 20px; fill: var(--ink-white); }
  .partners { font-family: "Lato", sans-serif; font-style: italic; font-size: 19px; fill: var(--ink-grey); }
  .partner-kelvo { font-family: "Lato", sans-serif; font-weight: 700; font-size: 17px; fill: var(--partner-green); }
  .partner-brightmold { font-family: "Lato", sans-serif; font-weight: 700; font-size: 13px; fill: var(--partner-blue); }
</style>
</head>
<body>
<main class="canvas">

  <svg class="card card--front" viewBox="0 0 825 473" xmlns="http://www.w3.org/2000/svg" aria-label="Business card front">
    <defs>
      <linearGradient id="paperFade" x1="0" y1="0" x2="1" y2="1">
        <stop offset="0" stop-color="var(--paper-grey)"/>
        <stop offset="0.5" stop-color="var(--paper-white)"/>
        <stop offset="1" stop-color="var(--paper-grey)"/>
      </linearGradient>
      <linearGradient id="panelBlue" x1="0" y1="0" x2="1" y2="1">
        <stop offset="0" stop-color="var(--blue-deep)"/>
        <stop offset="0.6" stop-color="var(--blue-mid)"/>
        <stop offset="1" stop-color="var(--blue-light)"/>
      </linearGradient>
      <linearGradient id="stripeOrange" x1="0" y1="0" x2="1" y2="0">
        <stop offset="0" stop-color="var(--orange)"/>
        <stop offset="1" stop-color="var(--orange-light)"/>
      </linearGradient>
    </defs>
    <rect class="card-paper" width="825" height="473" fill="url(#paperFade)"/>
    <polygon class="accent-stripe" points="462,0 480,0 336,232 510,473 486,473 318,232" fill="url(#stripeOrange)"/>
    <polygon class="contact-panel" points="0,0 462,0 318,232 486,473 0,473" fill="url(#panelBlue)"/>
    <polyline class="panel-frame" points="452,8 8,8 8,465 470,465" fill="none" stroke="var(--blue-edge)" stroke-width="3"/>
    <polyline class="panel-edge" points="462,0 318,232 486,473" fill="none" stroke="var(--blue-edge)" stroke-width="4"/>

    <text class="name" x="55" y="128">MARCUS LIN</text>
    <text class="role" x="55" y="156">DIRECTOR</text>

    <text class="detail" x="55" y="204">Factory K4, 7B</text>
    <text class="detail" x="55" y="229">Harlowe Road, Springvale</text>
    <text class="detail" x="55" y="254">Victoria, Australia 3150</text>

    <text class="detail" x="55" y="300">P. +61-3-8555 6413</text>
    <text class="detail" x="55" y="326">marcus.lin@vortalmake.com.au</text>
    <text class="detail" x="55" y="353">www.vortalmake.com.au</text>

    <rect class="brand-square" x="530" y="225" width="26" height="26" fill="var(--orange)"/>
    <text class="brand-name" x="568" y="250" font-size="30">VORTAL</text>
    <text class="brand-name" x="530" y="292" font-size="30">MAKE</text>
  </svg>

  <svg class="card card--back" viewBox="0 0 825 473" xmlns="http://www.w3.org/2000/svg" aria-label="Business card back">
    <rect class="card-paper" width="825" height="473" fill="var(--card-black)"/>

    <rect class="brand-square" x="264" y="190" width="40" height="40" fill="var(--orange)"/>
    <text class="brand-name brand-name--back" x="318" y="228" font-size="46">VORTAL MAKE</text>

    <line x1="144" y1="373" x2="204" y2="373" stroke="var(--ink-white)" stroke-width="1"/>
    <text class="tagline" x="412" y="380" text-anchor="middle">Leading supplier 3D Filaments &amp; 3D Printers</text>
    <line x1="622" y1="373" x2="682" y2="373" stroke="var(--ink-white)" stroke-width="1"/>

    <text class="partners" x="143" y="412">Authorised distributor</text>
    <text class="partner-kelvo" x="334" y="412">Kelvo</text>
    <text class="partners" x="391" y="412">Authorised reseller</text>
    <rect x="554" y="399" width="13" height="13" fill="var(--partner-blue)"/>
    <text class="partner-brightmold" x="572" y="410">Brightmold</text>
    <text class="partners" x="641" y="412">in</text>
    <rect class="country-badge" x="660" y="398" width="26" height="16" fill="var(--flag-navy)"/>
  </svg>

</main>
</body>
</html>
```